Creative, fresh business card design for Ripplecraft Facades

We need a fresh, creative business card design for Ripplecraft Facades. We are the manufacturer of Ripplecraft Facades in Australia. Wall panels are 2400 x 1200mm panels made from MDF and feature 3D patterns on the face of the panel. The colours to be used are green, silver/grey and white RGB
Red 187
Green 207
Blue 65.

An idea is to possibly use a watermark of one of our designs as a background (like on the "Grids" design on the left hand side of page 2 of our brochure).

Target Market(s)

Interior designers, architects, builders and home renovators

Industry/Entity Type

Business

Contact Information for Business Card

Details to go on the card are:
Our logo (attached),
Slogan: "Decorative panels for interiors and exteriors",
Contact name,
Position,
Mobile phone number,
Business address,
Business phone,
Business fax,
Website and
Email address.

I have attached a few images of our panels and our brochure for reference.

The colours of the business card should feature our logo colours which are: RGB
Red 187
Green 207
Blue 65

Requirements
Must have
• Very modern fonts and design. Some of the designs shown especially the "Prisms" design which is a popular design.
Nice to have
• Creative but simple design. Very contemporary.
Should not have
• Anything ornate or old fashioned.

```html
<!DOCTYPE html>
<html lang="en">
<head>
<meta charset="utf-8">
<title>Ripplecraft Facades – Business Card</title>
<link rel="stylesheet" href="https://fonts.googleapis.com/css2?family=Open+Sans:wght@400;600;700&display=swap">
<style>
  :root {
    --brand-green: rgb(187, 207, 65);
    --brand-green-soft: #c9da6a;
    --silver: #8c8e93;
    --ink: #3e3f42;
    --ink-soft: #5a5b5e;
    --card-white: #ffffff;
    --backdrop: #2a2a2c;
  }
  * { margin: 0; padding: 0; box-sizing: border-box; }
  html, body {
    width: 1200px; height: 1000px; overflow: hidden;
    background: var(--backdrop);
    font-family: "Open Sans", Arial, sans-serif;
  }
  .card {
    position: absolute; left: 100px; top: 200px;
    width: 1000px; height: 600px;
    background: var(--card-white);
    border-radius: 48px;
    overflow: hidden;
  }
  .card__swoosh { position: absolute; inset: 0; width: 100%; height: 100%; }

  .brand {
    position: absolute; left: 250px; top: 210px;
    display: flex; align-items: center; gap: 10px;
    font-size: 28px; font-weight: 700; color: var(--brand-green);
    line-height: 1.1;
  }
  .brand__dot { width: 18px; height: 18px; background: var(--brand-green); flex: none; }

  .person { position: absolute; left: 330px; top: 420px; }
  .person__name { font-size: 36px; font-weight: 700; color: var(--ink); }
  .person__name span { color: var(--brand-green); }
  .person__role { font-size: 24px; color: var(--ink-soft); margin-top: -4px; }

  .divider {
    position: absolute; left: 610px; top: 330px;
    width: 2px; height: 170px; background: var(--ink-soft);
  }

  .address {
    position: absolute; left: 640px; top: 95px;
    display: flex; gap: 18px; align-items: flex-start;
    font-size: 22px; color: var(--ink-soft); line-height: 1.3;
  }
  .address svg { margin-top: 36px; }

  .contacts {
    position: absolute; left: 640px; top: 270px; list-style: none;
    font-size: 24px; color: var(--ink-soft); line-height: 1.45;
  }
  .contacts li { display: flex; align-items: center; gap: 20px; }
  .contacts svg { width: 18px; height: 18px; flex: none; }
</style>
</head>
<body>
  <article class="card">
    <svg class="card__swoosh" viewBox="0 0 1000 600" aria-hidden="true">
      <path d="M0 0 H255 C150 150 160 420 330 600 H0 Z" fill="var(--brand-green)"/>
      <path d="M215 110 C150 280 200 470 300 600 H255 C170 480 150 300 215 110 Z" fill="var(--brand-green-soft)" opacity="0.7"/>
      <path d="M200 300 C200 430 260 530 360 600 H285 C215 510 190 410 200 300 Z" fill="var(--silver)"/>
    </svg>

    <div class="brand"><span class="brand__dot"></span>Ripplecraft Facades</div>

    <div class="person">
      <div class="person__name">Elena <span>Marsh</span></div>
      <div class="person__role">Director</div>
    </div>

    <div class="divider"></div>

    <div class="address">
      <svg width="26" height="26" viewBox="0 0 24 24" fill="none" stroke="var(--brand-green)" stroke-width="1.6" stroke-linejoin="round"><path d="M22 2 L2 10 L11 13 L14 22 Z"/></svg>
      <p>Your Street Address,<br>Harbor City, 1234</p>
    </div>

    <ul class="contacts">
      <li><svg viewBox="0 0 24 24" fill="none" stroke="var(--brand-green)" stroke-width="2"><rect x="7" y="2" width="10" height="20" rx="2"/></svg>+000 123 456 789</li>
      <li><svg viewBox="0 0 24 24" fill="var(--brand-green)"><path d="M6 2 L10 6 L8 9 C9 12 12 15 15 16 L18 14 L22 18 L19 22 C10 21 3 14 2 5 Z"/></svg>+000 123 456 789</li>
      <li><svg viewBox="0 0 24 24" fill="var(--brand-green)"><rect x="6" y="2" width="12" height="7"/><rect x="2" y="10" width="20" height="9" rx="2"/></svg>+000 123 456 789</li>
      <li><svg viewBox="0 0 24 24" fill="var(--brand-green)"><path d="M2 5 H22 V19 H2 Z M2 5 L12 13 L22 5" stroke="#fff" stroke-width="1.5"/></svg>elena@ripplecraft.com</li>
      <li><svg viewBox="0 0 24 24" fill="none" stroke="var(--brand-green)" stroke-width="3"><circle cx="14" cy="10" r="6"/><path d="M10 14 L3 21"/></svg>www.ripplecraft.com</li>
    </ul>
  </article>
</body>
</html>
```